New Website for World Wide Charity (KOLVAN)

We need a dynamic web design for our brand new charity organisation that will be working worldwide. We will be funded by donations so need to attract people to donate.

What We Do
We work to optimise the wellbeing of the planet, the animals and all that live within. Our slogan is Achieving Vibrational Equilibrium.

We have included a Powerpoint document which may help you understand what we need, it is just an idea for structure and style, it is not set in stone so feel free to be as creative as you like!
Updates

Designs look the same

Target Market(s)

Adults 18+ with an interest in animal, environmental. Businesses that may like to support our natural world or already support our natural world.

Number of Pages Required

3 page

Colors

Designer to choose colors to be used in the design.

Requirements
Must have
• We need the website to be easy to use and understand.

Web pages will be Home, What We Do, Who We Are, Success Stories, What You Can Do (Blog section), Seek Help, Donate, Join.
Nice to have
• Natural feel, easy to navigate, Ideally the website will look natural and organic.

Natural colours, blues, greens, sand, gold, brown, grey, silver, Orange and yellow for impact.
Should not have
• Should not have a dark coloured theme.

```html
<!DOCTYPE html>
<html lang="en">
<head>
<meta charset="utf-8">
<title>KOLVAN – Achieving Vibrational Equilibrium</title>
<link href="https://fonts.googleapis.com/css2?family=Montserrat:wght@500;600;700&family=Roboto:wght@300;400&display=swap" rel="stylesheet">
<style>
:root{
  --green:#3d8a41;
  --green-dark:#357a38;
  --green-deep:#2e6c31;
  --ink:#222;
  --body:#6b6b6b;
  --white:#fff;
  --mist:#eef0ee;
  --lilac:#e7dbe8;
  --ring:#6c7db0;
}
*{margin:0;padding:0;box-sizing:border-box}
html,body{width:1200px;height:3223px;overflow:hidden}
body{position:relative;background:var(--white);font-family:Roboto,Arial,sans-serif;color:var(--ink)}
a{text-decoration:none;color:inherit}

/* header */
.site-header{position:absolute;left:0;top:0;width:1200px;height:89px;background:var(--white);z-index:5}
.brand{position:absolute;left:50px;top:-55px;width:236px;height:236px;border-radius:50%;background:var(--white);z-index:6;display:flex;justify-content:center}
.brand-ring{width:178px;height:164px;border-radius:50%;border:3px solid var(--ring);background:var(--lilac);display:flex;align-items:center;justify-content:center;margin-top:61px}
.brand-name{font-family:Montserrat,sans-serif;font-weight:500;font-size:22px;color:var(--ring);letter-spacing:1px}
.main-nav{position:absolute;top:46px;left:0;font-size:14px;color:var(--ink)}
.main-nav a{position:absolute;white-space:nowrap}
.main-nav a.active{color:var(--green)}
.btn{display:flex;align-items:center;justify-content:center;border-radius:30px;font-family:Montserrat,sans-serif;font-weight:600;text-transform:uppercase;position:absolute}
.btn-solid{background:var(--green);color:var(--white);box-shadow:0 2px 4px rgba(0,0,0,.15)}
.btn-outline{border:1.5px solid var(--green);color:var(--green);background:var(--white)}

/* hero */
.hero{position:absolute;left:0;top:89px;width:1200px;height:729px;
  background:
   linear-gradient(180deg,rgba(0,0,0,0) 55%,rgba(10,20,10,.35) 100%),
   radial-gradient(ellipse 90px 150px at 860px 120px,#a9aca6 0%,rgba(140,146,140,.6) 50%,rgba(0,0,0,0) 100%),
   radial-gradient(ellipse 160px 200px at 740px 330px,#7d8580 0%,rgba(95,104,100,.6) 50%,rgba(0,0,0,0) 100%),
   radial-gradient(ellipse 230px 230px at 520px 600px,#24343a 0%,rgba(34,50,55,.8) 50%,rgba(0,0,0,0) 100%),
   radial-gradient(ellipse 520px 360px at 180px 160px,#7c8a2e 0%,rgba(90,110,35,.6) 55%,rgba(0,0,0,0) 100%),
   radial-gradient(ellipse 420px 300px at 1080px 250px,#6f8428 0%,rgba(80,100,30,.5) 55%,rgba(0,0,0,0) 100%),
   linear-gradient(160deg,#55682a 0%,#3a5520 40%,#2a4219 70%,#1f3315 100%)}
.hero-title{position:absolute;top:298px;width:100%;text-align:center;font-family:Montserrat,sans-serif;font-weight:700;font-size:35px;color:var(--white);text-shadow:0 1px 6px rgba(0,0,0,.3)}
.hero-sub{position:absolute;top:356px;width:100%;text-align:center;font-family:Montserrat,sans-serif;font-weight:500;font-size:25px;color:var(--white);text-shadow:0 1px 6px rgba(0,0,0,.3)}

/* pillars */
.pillar-img{position:absolute;top:918px;width:317px;height:269px;box-shadow:0 1px 4px rgba(0,0,0,.12)}
.pillar-title{position:absolute;top:1214px;width:317px;text-align:center;font-family:Montserrat,sans-serif;font-weight:600;font-size:19px;letter-spacing:.5px}
.pillar .btn{top:1254px;width:171px;height:51px;font-size:16px}

/* features */
.feature-img{position:absolute}
.feature-title{position:absolute;font-family:Montserrat,sans-serif;font-weight:600;font-size:19px;letter-spacing:.5px}
.feature-text{position:absolute;width:450px;font-size:15.5px;font-weight:300;line-height:34.3px;color:var(--body)}
.mist{position:absolute;left:0;top:2560px;width:1200px;height:287px;background:linear-gradient(180deg,rgba(238,240,238,0) 0%,var(--mist) 100%)}

/* footer */
.site-footer{position:absolute;left:0;top:2847px;width:1200px;height:331px;background:var(--green-dark);color:var(--white)}
.footer-brand{position:absolute;left:193px;top:72px;width:193px;height:193px;border-radius:50%;border:3px solid var(--ring);background:var(--lilac);display:flex;align-items:center;justify-content:center}
.footer-brand .brand-name{font-size:22px;color:var(--white)}
.footer-col{position:absolute;top:80px}
.footer-col h4{font-family:Montserrat,sans-serif;font-weight:600;font-size:15.5px;letter-spacing:.3px}
.footer-col h4::after{content:"";display:block;width:39px;height:3px;background:var(--white);margin-top:11px}
.footer-col ul{list-style:none;margin-top:25px}
.footer-col li{font-size:15.5px;height:36.7px}
.footer-bar{position:absolute;left:0;top:3178px;width:1200px;height:45px;background:var(--green-deep);color:var(--white);font-size:15.5px}
.footer-bar span{position:absolute;top:12px}
</style>
</head>
<body>

<header class="site-header">
  <nav class="main-nav">
    <a class="active" style="left:337px">Home</a>
    <a style="left:399px">What We Do</a>
    <a style="left:499px">Who We Are</a>
    <a style="left:600px">Success Stories</a>
    <a style="left:724px">What You Can Do</a>
  </nav>
  <a class="btn btn-solid" style="left:871px;top:34px;width:131px;height:39px;font-size:14px;font-weight:500">Donate</a>
  <a class="btn btn-outline" style="left:1015px;top:33px;width:107px;height:40px;font-size:14px;font-weight:500">Join</a>
</header>
<div class="brand"><div class="brand-ring"><span class="brand-name">KOLVAN</span></div></div>

<section class="hero" role="img" aria-label="Aerial view of a winding lake through dense green forest">
  <h1 class="hero-title">HELP RAISE WORLD VIBRATION</h1>
  <p class="hero-sub">Achieving Vibrational Equilibrium</p>
  <a class="btn btn-solid" style="left:470px;top:413px;width:257px;height:50px;font-size:16px">Make a Difference</a>
</section>

<section class="pillars">
  <div class="pillar">
    <div class="pillar-img" style="left:113px;background:linear-gradient(180deg,rgba(0,0,0,0) 70%,#3a2a22 100%),radial-gradient(ellipse 120px 90px at 45% 68%,#9fd246 0%,rgba(110,170,40,.5) 60%,rgba(0,0,0,0) 100%),linear-gradient(135deg,#b98a70 0%,#5c8f2a 30%,#2f6a18 65%,#163a12 100%)" role="img" aria-label="Hand watering a young seedling"></div>
    <h3 class="pillar-title" style="left:113px">ENVIRONMENT</h3>
    <a class="btn btn-solid" style="left:186px">Find Out More</a>
  </div>
  <div class="pillar">
    <div class="pillar-img" style="left:440px;background:radial-gradient(ellipse 130px 120px at 52% 48%,#7a4f2c 0%,#60401f 55%,rgba(0,0,0,0) 100%),linear-gradient(135deg,#5d6a48 0%,#6e6e52 45%,#4d5a3a 100%)" role="img" aria-label="Brown bear walking through the woods"></div>
    <h3 class="pillar-title" style="left:440px">ANIMAL</h3>
    <a class="btn btn-solid" style="left:513px">Find Out More</a>
  </div>
  <div class="pillar">
    <div class="pillar-img" style="left:768px;background:radial-gradient(ellipse 60px 90px at 52% 55%,#b6d244 0%,rgba(160,190,60,.4) 60%,rgba(0,0,0,0) 100%),linear-gradient(180deg,#2f3a2c 0%,#a6ad9c 30%,#6b705e 55%,#8a4b2a 80%,#6b3a20 100%)" role="img" aria-label="Hiker standing on a forest trail"></div>
    <h3 class="pillar-title" style="left:768px">HUMAN</h3>
    <a class="btn btn-solid" style="left:840px">Find Out More</a>
  </div>
</section>

<section class="feature">
  <h2 class="feature-title" style="left:114px;top:1491px">ENVIRONMENT</h2>
  <p class="feature-text" style="left:113px;top:1535px">Lorem ipsum dolor sit amet, consectetur adipiscing elit, sed do eiusmod tempor incididunt ut labore et dolore magna aliqua. Ut enim ad minim veniam, quis nostrud exercitation ullamco laboris nisi ut aliquip ex ea commodo consequat. Duis aute irure dolor in reprehenderit in voluptate velit esse cillum dolore eu fugiat nulla pariatur. Excepteur sint occaecat cupidatat non proident</p>
  <div class="feature-img" style="left:593px;top:1409px;width:607px;height:414px;background:radial-gradient(ellipse 90px 110px at 33% 72%,#6fb59a 0%,rgba(100,170,140,.5) 60%,rgba(0,0,0,0) 100%),radial-gradient(ellipse 200px 220px at 82% 55%,#2d93b4 0%,rgba(40,140,175,.6) 60%,rgba(0,0,0,0) 100%),linear-gradient(120deg,#4b5633 0%,#6a6a4c 40%,#3d3a2c 75%,#23221d 100%)" role="img" aria-label="Volunteers collecting litter in a forest"></div>
</section>

<section class="feature">
  <div class="feature-img" style="left:0;top:1872px;width:608px;height:414px;background:radial-gradient(ellipse 150px 170px at 68% 50%,#efeee8 0%,#3a3a38 55%,rgba(0,0,0,0) 100%),linear-gradient(180deg,rgba(0,0,0,0) 65%,#8aa046 100%),linear-gradient(120deg,#8e6a48 0%,#a47a52 35%,#6d5a45 70%,#4c4a3f 100%)" role="img" aria-label="Giant panda eating bamboo among rocks"></div>
  <h2 class="feature-title" style="left:645px;top:1954px">ANIMAL</h2>
  <p class="feature-text" style="left:644px;top:1998px">Lorem ipsum dolor sit amet, consectetur adipiscing elit, sed do eiusmod tempor incididunt ut labore et dolore magna aliqua. Ut enim ad minim veniam, quis nostrud exercitation ullamco laboris nisi ut aliquip ex ea commodo consequat. Duis aute irure dolor in reprehenderit in voluptate velit esse cillum dolore eu fugiat nulla pariatur. Excepteur sint occaecat cupidatat non proident</p>
</section>

<div class="mist"></div>

<section class="feature">
  <h2 class="feature-title" style="left:114px;top:2414px">HUMAN</h2>
  <p class="feature-text" style="left:113px;top:2458px">Lorem ipsum dolor sit amet, consectetur adipiscing elit, sed do eiusmod tempor incididunt ut labore et dolore magna aliqua. Ut enim ad minim veniam, quis nostrud exercitation ullamco laboris nisi ut aliquip ex ea commodo consequat. Duis aute irure dolor in reprehenderit in voluptate velit esse cillum dolore eu fugiat nulla pariatur. Excepteur sint occaecat cupidatat non proident</p>
  <div class="feature-img" style="left:593px;top:2332px;width:607px;height:413px;background:radial-gradient(ellipse 110px 190px at 78% 65%,#1f9cc0 0%,rgba(30,140,175,.6) 60%,rgba(0,0,0,0) 100%),radial-gradient(ellipse 180px 160px at 15% 15%,#a7952f 0%,rgba(140,130,40,.5) 60%,rgba(0,0,0,0) 100%),linear-gradient(120deg,#5c5f25 0%,#3a4a22 35%,#202a1e 70%,#1a1f1c 100%)" role="img" aria-label="Woman in a blue rain jacket enjoying the rain"></div>
</section>

<footer class="site-footer">
  <div class="footer-brand"><span class="brand-name">KOLVAN</span></div>
  <div class="footer-col" style="left:512px">
    <h4>GET INVOLVED</h4>
    <ul><li>Join Us</li><li>Fundraise</li><li>Donate</li><li>Shop</li></ul>
  </div>
  <div class="footer-col" style="left:701px">
    <h4>GET HELP</h4>
    <ul><li>Contact Us</li><li>Media</li></ul>
  </div>
  <div class="footer-col" style="left:862px">
    <h4>LEGAL</h4>
    <ul><li>Terms and Conditions</li><li>Cookies</li><li>Privacy Policy</li></ul>
  </div>
</footer>
<div class="footer-bar">
  <span style="left:113px">Charity Number - 0000-45698-bcv</span>
  <span style="right:112px">© 2021 All Rights Reserved</span>
</div>

</body>
</html>
```